New Webpage for High Class Expert Witness Services Company

We are looking for a minimalist design for a webpage that just has our logo and an entry form offer to connect with one of our Liaisons.
The entry form should just ask for Name, Email, Contact Info and Description of Project.

Company Name is: The Marlowe Crest Advisory Services

Number of Pages Required

1 page

```html
<!DOCTYPE html>
<html lang="en">
<head>
<meta charset="utf-8">
<title>Marlowe Crest Advisory Services</title>
<link rel="stylesheet" href="https://fonts.googleapis.com/css2?family=Cinzel:wght@400;600;700&family=Roboto:wght@400&display=swap">
<style>
  :root {
    --page-bg: #e2e2e2;
    --page-bg-light: #ececec;
    --ink: #1e1e1e;
    --ink-soft: #3a3a3a;
    --panel-bg: #efefef;
    --panel-border: #d0d0d0;
    --field-border: #8f8f8f;
    --field-bg: #ececec;
    --rule: #cfcfcf;
    --button-text: #ffffff;
  }
  * { box-sizing: border-box; margin: 0; padding: 0; }
  html, body { width: 1200px; height: 739px; overflow: hidden; }
  body {
    position: relative;
    background: radial-gradient(ellipse at 45% 40%, var(--page-bg-light) 0%, var(--page-bg) 70%);
    font-family: "Roboto", Arial, sans-serif;
    color: var(--ink);
  }
  .backdrop-art {
    position: absolute;
    left: 350px; top: 118px;
    width: 380px; height: 480px;
    background: radial-gradient(ellipse at 40% 30%, #c9c9c9 0%, #dcdcdc 45%, rgba(226,226,226,0) 75%);
  }
  .brand {
    position: absolute;
    left: 133px; top: 50px;
    display: flex; align-items: center; gap: 14px;
  }
  .brand-mark {
    width: 44px; height: 44px;
    background: var(--ink-soft);
  }
  .brand-name {
    font-family: "Cinzel", Georgia, serif;
    font-weight: 600;
    font-size: 24px;
    line-height: 1.05;
    color: var(--ink-soft);
  }
  .phone {
    position: absolute;
    right: 119px; top: 40px;
    font-family: "Cinzel", Georgia, serif;
    font-size: 32px;
    color: var(--ink);
  }
  .hero {
    position: absolute;
    left: 136px; top: 268px;
    font-family: "Cinzel", Georgia, serif;
  }
  .hero-kicker {
    font-size: 18px;
    letter-spacing: 2.2px;
    margin-left: 3px;
    color: var(--ink-soft);
  }
  .hero-title {
    margin-top: 14px;
    font-weight: 400;
    font-size: 51px;
    line-height: 58px;
    letter-spacing: 1.5px;
    color: var(--ink);
  }
  .liaison-form {
    position: absolute;
    left: 716px; top: 124px;
    width: 379px; height: 438px;
    background: var(--panel-bg);
    border: 1px solid var(--panel-border);
    padding: 34px 45px 0 46px;
  }
  .form-title {
    font-family: "Cinzel", Georgia, serif;
    font-weight: 400;
    font-size: 21.5px;
    letter-spacing: 0.6px;
    margin-bottom: 22px;
    white-space: nowrap;
  }
  .field {
    display: block;
    width: 295px; height: 42px;
    margin-bottom: 13px;
    padding: 0 17px;
    border: 1px solid var(--field-border);
    border-radius: 2px;
    background: var(--field-bg);
    font-family: "Roboto", Arial, sans-serif;
    font-size: 13px;
    color: var(--ink);
  }
  .field::placeholder { color: var(--ink); }
  .field-area {
    height: 88px;
    padding-top: 9px;
    resize: none;
  }
  .submit {
    display: block;
    width: 298px; height: 44px;
    margin-top: -1px;
    border: none; border-radius: 2px;
    background: var(--ink);
    color: var(--button-text);
    font-family: "Cinzel", Georgia, serif;
    font-weight: 700;
    font-size: 16px;
  }
  .site-footer {
    position: absolute;
    left: 0; top: 680px;
    width: 1200px; height: 59px;
    border-top: 1px solid var(--rule);
    text-align: center;
    padding-top: 21px;
    font-size: 12px;
    color: var(--ink);
  }
</style>
</head>
<body>
  <div class="backdrop-art" role="img" aria-label="Soft grey faceted emblem background artwork"></div>

  <header>
    <div class="brand">
      <span class="brand-mark"></span>
      <span class="brand-name">Marlowe Crest<br>Advisory Services</span>
    </div>
    <div class="phone">Call 800-555-0142</div>
  </header>

  <main>
    <section class="hero">
      <p class="hero-kicker">MARLOWE CREST ADVISORY SERVICES</p>
      <h1 class="hero-title">SEAMLESS<br>MEDICAL EXPERT<br>INTEGRATION</h1>
    </section>

    <form class="liaison-form">
      <h2 class="form-title">CONNECT WITH A LIAISON</h2>
      <input class="field" type="text" placeholder="Name*">
      <input class="field" type="email" placeholder="Email*">
      <input class="field" type="tel" placeholder="Phone number*">
      <textarea class="field field-area" placeholder="Description of Project"></textarea>
      <button class="submit" type="button">SUBMIT</button>
    </form>
  </main>

  <footer class="site-footer">© 2026 Marlowe Crest Advisory Services. All Rights Reserved</footer>
</body>
</html>
```